Halcyon Electrical Services Website

'Mossgrove Electrical Services' is a leading electrician company based in Hertfordshire. We are a VORTIN approved and registered company in the UK. We are also registered to carry out electrical installations under Part P of the building regulations. As part of a wide range of electrical services, we have professional expertise in installation testing (landlords, periodic, insurance, emergency lighting & fire alarms) rewires, installations, electrical maintenance, security systems & portable appliance testing (PAT). We provide a bespoke service to suite the needs of High End clients so the site must reflect the type of clientele we are targeting

WE ARE A SMALL COMPANY AND ARE LOOKING FOR THE DESIGNERS TO ALSO IMPLEMENT THIS ONTO OUR DOMAIN NAME SO ITS A FULLY FUNCTIONAL FOR OUR CLIENTS WHEN WE FINISH THIS SIMPLE PROJECT

Target Market(s)

Estate Agents, High End Clients that require intallations in Multi Million pound houses

Industry/Entity Type

Electrician

Font styles to use
Serif
Sans Serif
Other font styles liked:
• Chose an elegant professional font

Requirements
Must have
• please look at www.mossgroveelectrical.example (the current old site is down, and will go live in 24-48 hours so please get the content from there)

Luxury design, a wow factor when high end clients logon

the logo is Blue so a blue colour these for the branding is essential. We are open to your design ideas around the logo.

VORTIN and Part P and Wiring Assurance Board are safety regulations so please add the logos a place on the site together.
Nice to have
• your creative input
Should not have
• to many conflicting colours, too many horrible bright colours

```html
<!DOCTYPE html>
<html lang="en">
<head>
<meta charset="utf-8">
<title>Mossgrove Electrical Services Ltd</title>
<link href="https://fonts.googleapis.com/css2?family=Source+Sans+3:wght@300;400;600&display=swap" rel="stylesheet">
<style>
:root{
  --brand:#1f3a93;
  --brand-dark:#1a2f7a;
  --brand-light:#2d4fb3;
  --ink:#4a4a4a;
  --muted:#8a8a8a;
  --rule:#dcdcdc;
  --hero-bg:#e8e8e8;
  --white:#fff;
}
*{box-sizing:border-box;margin:0;padding:0}
html,body{width:876px;height:1200px;overflow:hidden;background:var(--white)}
body{font-family:"Source Sans 3",sans-serif;color:var(--ink);position:relative}
.abs{position:absolute}

.brand{left:86px;top:44px;display:flex;align-items:center;gap:8px}
.brand-mark{width:20px;height:20px;border-radius:50%;background:var(--brand)}
.brand-name{font-size:8.5px;font-weight:600;color:var(--brand);line-height:1.2;letter-spacing:.4px;width:70px}
.contact{right:94px;top:54px;text-align:right}
.contact-email{font-size:10px;color:#222}
.contact-phone{font-size:19px;font-weight:600;color:var(--brand);display:flex;align-items:center;gap:3px;justify-content:flex-end;margin-top:1px}

.nav{left:0;top:96px;width:876px;height:42px;background:linear-gradient(var(--brand-light),var(--brand-dark))}
.nav ul{list-style:none;display:flex;position:absolute;left:86px;top:0;height:42px}
.nav li{color:var(--white);font-size:13px;font-weight:600;padding:0 12px;line-height:42px;border-right:1px solid rgba(255,255,255,.18)}
.search{position:absolute;left:621px;top:12px;width:161px;height:20px;background:#1a2c6b;color:#8896c0;font-size:9px;padding:4px 8px}
.search svg{position:absolute;right:4px;top:3px}

.hero{left:0;top:138px;width:876px;height:272px;background:var(--hero-bg);box-shadow:0 6px 8px -4px rgba(0,0,0,.45)}
.hero-photo{position:absolute;right:0;top:0;width:443px;height:272px;background:linear-gradient(120deg,#c9c9c4,#8e8a80 45%,#4b4a48 80%,#a9a9a2)}
.hero-kicker{position:absolute;left:93px;top:108px;font-size:26px;font-weight:300;color:var(--brand)}
.hero-title{position:absolute;left:93px;top:134px;font-size:52px;font-weight:600;color:#444;line-height:1}
.dots{position:absolute;left:98px;top:201px;display:flex;gap:4px}
.dots i{width:11px;height:11px;border-radius:50%;background:#4a4a4a}
.dots i:first-child{background:var(--brand)}

.section-title{color:var(--brand);font-weight:600;font-size:15px}
.welcome{left:93px;top:440px;width:690px;text-align:center}
.welcome p{margin-top:8px;font-size:9.2px;line-height:17.6px;color:var(--muted);text-align:justify;text-align-last:center}

.services-head{left:93px;top:572px;width:690px;height:24px;border-bottom:1px solid var(--rule);text-align:center}
.services-head svg{position:absolute;top:2px}
.card{top:605px;width:220px;height:122px;border:4px solid #cfcfcf;background:#f4fafb}
.card-pic{position:absolute;left:22px;top:10px;width:78px;height:98px;background:linear-gradient(#e8c23a,#d6a21a)}
.card-label{position:absolute;left:106px;top:50px;font-size:11px;font-weight:600;color:var(--brand-dark)}
.card-copy{top:741px;width:221px;font-size:9.2px;line-height:17.6px;color:var(--muted);text-align:justify}
.btn{top:820px;width:56px;height:18px;background:var(--brand);color:var(--white);font-size:7px;font-weight:600;line-height:18px;text-align:center}

.testi-head{left:93px;top:864px;width:396px;height:25px;border-bottom:1px solid var(--rule)}
.avatar{left:95px;top:927px;width:103px;height:103px;border-radius:50%;background:#b8b4ae;border:4px solid #e6e6e6}
.quote-mark{left:198px;top:896px;font-size:34px;font-weight:600;color:#555;line-height:1}
.quote{left:213px;top:918px;width:276px;font-size:9.4px;line-height:17.6px;color:#555;text-align:justify}
.quote-by{left:213px;top:1055px;font-size:11px;font-weight:600;color:var(--brand)}

.news-head{left:504px;top:864px;width:278px;height:25px;border-bottom:1px solid var(--rule)}
.news-pic{left:504px;width:99px;height:58px;background:linear-gradient(120deg,#6f87a5,#b4b9bd 55%,#3e4a59)}
.news-copy{left:612px;width:170px;font-size:9px;line-height:17.6px;color:var(--muted)}
.news-date{color:var(--brand);font-size:9px}

.footer{left:0;top:1130px;width:876px;height:70px;background:linear-gradient(var(--brand-light),var(--brand-dark))}
.footer-nav{position:absolute;left:94px;top:15px;display:flex;font-size:10.5px;color:var(--white)}
.footer-nav span{padding:0 13px}
.footer-nav span:first-child{padding-left:0}
.footer-nav b{font-weight:400;opacity:.8}
.copy{position:absolute;left:207px;top:38px;font-size:10.5px;color:var(--white)}
.badges{position:absolute;left:605px;top:18px;display:flex;gap:14px;align-items:center}
.badge{background:rgba(255,255,255,.25)}
</style>
</head>
<body>

<header>
  <div class="abs brand"><span class="brand-mark"></span><span class="brand-name">MOSSGROVE ELECTRICAL SERVICES LTD</span></div>
  <div class="abs contact">
    <div class="contact-email">Email: hello@mossgrove.example</div>
    <div class="contact-phone">
      <svg width="11" height="14" viewBox="0 0 11 14"><path d="M2 1l2.5-.5 1.3 3-1.5 1.2c.6 1.8 1.5 3.2 2.8 4.3l1.5-1 2.2 2.3-1.6 2C5 11.8 1.2 6.5 2 1z" fill="#333"/></svg>
      555.014.2280
    </div>
  </div>
</header>

<nav class="abs nav">
  <ul>
    <li>Home</li><li>About Us</li><li>Services</li><li>Solutions</li><li>Testimonials</li><li>FAQ’s</li><li>Contact Us</li>
  </ul>
  <div class="search">Search
    <svg width="14" height="14" viewBox="0 0 14 14"><circle cx="5.5" cy="5.5" r="4" fill="none" stroke="#9aa6c8" stroke-width="1.6"/><path d="M8.5 8.5l4 4" stroke="#9aa6c8" stroke-width="2"/></svg>
  </div>
</nav>

<section class="abs hero">
  <div class="hero-photo" role="img" aria-label="Two electricians in hard hats working on a distribution board"></div>
  <div class="hero-kicker">Mossgrove Electrical</div>
  <div class="hero-title">Services</div>
  <div class="dots"><i></i><i></i><i></i><i></i></div>
</section>

<section class="abs welcome">
  <h2 class="section-title">WELCOME TO MOSSGROVE ELECTRICAL SERVICES LTD</h2>
  <p>Sed ut perspiciatis unde omnis iste natus error sit voluptatem accusantium doloremque laudantium, totam rem aperiam, eaque ipsa quae ab illo inventore veritatis et quasi architecto beatae vitae dicta sunt explicabo. Nemo enim ipsam voluptatem quia voluptas sit aspernatur aut odit aut fugit, sed quia consequuntur magni dolores eos qui ratione voluptatem sequi nesciunt. Neque porro quisquam est, qui dolorem ipsum quia dolor sit amet, consectetur, adipisci velit, sed quia non numquam eius modi tempora incidunt ut labore et dolore magnam aliquam quaerat voluptatem.</p>
</section>

<div class="abs services-head">
  <svg style="left:2px" width="12" height="18" viewBox="0 0 12 18"><path d="M10 2L3 9l7 7" fill="none" stroke="#333" stroke-width="3"/></svg>
  <h2 class="section-title">SERVICES</h2>
  <svg style="right:2px" width="12" height="18" viewBox="0 0 12 18"><path d="M2 2l7 7-7 7" fill="none" stroke="#333" stroke-width="3"/></svg>
</div>

<div class="abs card" style="left:93px">
  <div class="card-pic" role="img" aria-label="Yellow installation tester case"></div>
  <div class="card-label">Installation Testing</div>
</div>
<div class="abs card" style="left:328px">
  <div class="card-pic" role="img" aria-label="Digital multimeter with probes" style="background:linear-gradient(#e09a2a,#3b3b3b)"></div>
  <div class="card-label" style="left:136px">Installations</div>
</div>
<div class="abs card" style="left:562px;background:#fff">
  <div class="card-pic" role="img" aria-label="Coloured copper cable ends" style="background:linear-gradient(90deg,#3b7fc4,#9cbb38,#8a4a22)"></div>
  <div class="card-label" style="left:110px">Rewires.</div>
</div>

<p class="abs card-copy" style="left:93px">Sed ut perspiciatis unde omnis iste natus error sit voluptatem accusantium doloremque laudantium, totam rem aperiam, eaque ipsa quae ab illo inventore veritatis et quasi architecto beatae vitae dicta sunt explicabo.</p>
<p class="abs card-copy" style="left:329px">Sed ut perspiciatis unde omnis iste natus error sit voluptatem accusantium doloremque laudantium, totam rem aperiam, eaque ipsa quae ab illo inventore veritatis et quasi architecto beatae vitae dicta sunt explicabo.</p>
<p class="abs card-copy" style="left:561px">Sed ut perspiciatis unde omnis iste natus error sit voluptatem accusantium doloremque laudantium, totam rem aperiam, eaque ipsa quae ab illo inventore veritatis et quasi architecto beatae vitae dicta sunt explicabo.</p>

<div class="abs btn" style="left:93px">Read More</div>
<div class="abs btn" style="left:329px">Read More</div>
<div class="abs btn" style="left:560px">Read More</div>

<div class="abs testi-head"><h2 class="section-title">TESTIMONIALS</h2></div>
<div class="abs avatar" role="img" aria-label="Portrait of a client"></div>
<div class="abs quote-mark">“</div>
<p class="abs quote">Lorem Ipsum is simply dummy text of the printing and typesetting industry. Lorem Ipsum has been the industry's standard dummy text ever since the 1500s, when an unknown printer took a galley of type and scrambled it to make a type specimen book. It has survived not only five centuries, but also the leap into electronic typesetting, remaining essentially unchanged. It was popularised in the 1960s with the release of Quillmark sheets containing ..<b style="font-size:13px">”</b></p>
<div class="abs quote-by">By Daniel Ashcroft</div>

<div class="abs news-head"><h2 class="section-title">LATEST NEWS</h2></div>
<div class="abs news-pic" style="top:906px" role="img" aria-label="Electrician inspecting wiring"></div>
<p class="abs news-copy" style="top:902px">lOmnis iste natus error sit voluptatem accusantium doloremque laudantium, totam rem aperiam, eaque ipsa quae ab<br><span class="news-date">Posted On 23-11-2013</span></p>
<div class="abs news-pic" style="top:1006px;background:linear-gradient(120deg,#9fb2c4,#d9c27a 50%,#4f5966)" role="img" aria-label="Electrician working on a panel"></div>
<p class="abs news-copy" style="top:1001px">lOmnis iste natus error sit voluptatem accusantium doloremque laudantium, totam rem aperiam, eaque ipsa quae ab illo inventore veritatis et quasi<br><span class="news-date" style="display:block;margin-top:4px">Posted On 23-11-2013</span></p>

<footer class="abs footer">
  <div class="footer-nav">
    <span>Home</span><b>|</b><span>About Us</span><b>|</b><span>Services</span><b>|</b><span>Solutions</span><b>|</b><span>Testimonials</span><b>|</b><span>FAQ’s</span><b>|</b><span>Contact Us</span>
  </div>
  <div class="copy">Copyright© 2013 Company Name, All Rights Reserved</div>
  <div class="badges">
    <div class="badge" style="width:30px;height:28px"></div>
    <div class="badge" style="width:22px;height:26px"></div>
    <div class="badge" style="width:86px;height:12px"></div>
    <div class="badge" style="width:12px;height:12px"></div>
  </div>
</footer>

</body>
</html>
```